Business cards and stationary design

We just completed the design of our new logo and we need to print new business cards and letterhead for our nonprofit. We are looking for a fresh new design that shows off our new logo. On letterhead, we must have a column on the right or left to include our Board of Directors (up to 45 names) (see attachment)

Industry/Entity Type

Non-Profit

Contact Information for Business Card

Standard business card with name, title, Company name, mailing address phone numbers, email address and website. Tagline on back "Bringing the homeless home"

Font styles to use
Sans Serif

Requirements
Must have
• include pertinent information above
• new logo
• fonts compatible with logo
• should use logo colors only
Nice to have
• tag lines

```html
<!DOCTYPE html>
<html lang="en">
<head>
<meta charset="utf-8">
<title>Homeward Shelter Center — Business Card</title>
<link href="https://fonts.googleapis.com/css2?family=Saira:wght@500;600;700&family=Roboto:wght@400&display=swap" rel="stylesheet">
<style>
  :root {
    --backdrop: #2a2a2a;
    --brand-red: #d62027;
    --brand-teal: #1a87a3;
    --brand-yellow: #f4b223;
    --card-white: #f3f3f3;
    --text-grey: #4a4a4a;
    --white: #ffffff;
  }
  html, body {
    margin: 0;
    padding: 0;
    width: 1200px;
    height: 960px;
    overflow: hidden;
    background: var(--backdrop);
  }
  .canvas {
    position: relative;
    width: 1200px;
    height: 960px;
    font-family: "Saira", sans-serif;
  }
  .card {
    position: absolute;
    left: 320px;
    width: 600px;
    height: 342px;
    box-shadow: 0 6px 14px rgba(0,0,0,0.45);
    overflow: hidden;
  }
  .card-front {
    top: 105px;
    background: var(--brand-red);
  }
  .card-back {
    top: 493px;
    background: var(--card-white);
  }
  .front-name {
    position: absolute;
    left: 0;
    right: 0;
    top: 150px;
    text-align: center;
    color: var(--white);
    font-weight: 700;
    font-size: 34px;
    letter-spacing: 2px;
    text-transform: uppercase;
  }
  .front-web {
    position: absolute;
    left: 0;
    right: 0;
    top: 292px;
    text-align: center;
    color: var(--white);
    font-family: "Roboto", sans-serif;
    font-size: 15px;
    letter-spacing: 5.4px;
  }
  .back-brand {
    position: absolute;
    right: 36px;
    top: 92px;
    color: var(--brand-teal);
    font-weight: 600;
    font-size: 17px;
    letter-spacing: 2px;
    text-transform: uppercase;
  }
  .person-name {
    position: absolute;
    left: 30px;
    top: 142px;
    margin: 0;
    color: var(--brand-teal);
    font-weight: 700;
    font-size: 23px;
    line-height: 1;
    letter-spacing: -0.3px;
    text-transform: uppercase;
  }
  .person-title {
    position: absolute;
    left: 30px;
    top: 170px;
    margin: 0;
    color: var(--brand-red);
    font-weight: 600;
    font-size: 14px;
    text-transform: uppercase;
  }
  .address {
    position: absolute;
    left: 30px;
    top: 199px;
    margin: 0;
    color: var(--text-grey);
    font-weight: 600;
    font-size: 13px;
    line-height: 18px;
    font-style: normal;
  }
  .contact-line {
    position: absolute;
    left: 30px;
    display: flex;
    align-items: center;
    gap: 8px;
    color: var(--text-grey);
    font-weight: 600;
  }
  .contact-phone { top: 261px; font-size: 14px; }
  .contact-email { top: 282px; font-size: 13px; }
  .contact-icon { width: 14px; height: 14px; fill: var(--brand-teal); }
  .footer-bands {
    position: absolute;
    left: 0;
    bottom: 0;
    width: 600px;
    height: 33px;
  }
  .footer-web {
    position: absolute;
    left: 29px;
    bottom: 7px;
    color: var(--white);
    font-weight: 600;
    font-size: 13px;
    letter-spacing: 2.2px;
  }
</style>
</head>
<body>
<div class="canvas">

  <section class="card card-front">
    <div class="front-name">Homeward Shelter</div>
    <div class="front-web">www.homewardshelter.org</div>
  </section>

  <section class="card card-back">
    <div class="back-brand">Homeward Shelter Center</div>

    <h1 class="person-name">Daniel Reyes</h1>
    <p class="person-title">CEO/Founder</p>

    <address class="address">
      Homeward shelter center<br>
      1420 Willow Street<br>
      Fairbanks, Alaska 99701
    </address>

    <div class="contact-line contact-phone">
      <svg class="contact-icon" viewBox="0 0 24 24" aria-hidden="true">
        <path d="M6.6 10.8a15.1 15.1 0 0 0 6.6 6.6l2.2-2.2c.3-.3.7-.4 1-.2 1.1.4 2.3.6 3.6.6.6 0 1 .4 1 1V20c0 .6-.4 1-1 1C10.6 21 3 13.4 3 4c0-.6.4-1 1-1h3.5c.6 0 1 .4 1 1 0 1.3.2 2.5.6 3.6.1.3 0 .7-.2 1z"/>
      </svg>
      <span>555 214 0387</span>
    </div>

    <div class="contact-line contact-email">
      <svg class="contact-icon" viewBox="0 0 24 24" aria-hidden="true">
        <path d="M2 5h20v14H2z M3.5 6.5 12 12.5l8.5-6" fill="var(--brand-teal)"/>
        <path d="M3 6l9 6.5L21 6" fill="none" stroke="#fff" stroke-width="1.6"/>
      </svg>
      <span>daniel@homewardshelter.org</span>
    </div>

    <svg class="footer-bands" viewBox="0 0 600 33" aria-hidden="true">
      <rect x="285" y="20" width="315" height="13" fill="var(--brand-yellow)"/>
      <polygon points="0,0 268,0 300,33 0,33" fill="var(--brand-teal)"/>
    </svg>
    <div class="footer-web">www.homewardshelter.org</div>
  </section>

</div>
</body>
</html>
```